Modern Medical Optometry Website

We need mordern, Patient friendly website. Easy to navigate and enhance our advance medical technology and excellent patient care.
1. HOME PAGE
2. OUR TEAM PAGE
3. EYECARE PAGE - VISION SERVICES, EYE EXAMS, KERATOCONUS CENTER, GLAUCOMA , DIABITES, MELORIDEX EXAM, DIGITAL RETINAL, OCT.
4. MYOPIA CONTROL CLINIC
5. DRY EYE CLINIC
6. EYEWEAR
7. PATIENT CENTER - BLOG
7. CONTACT US
This is our current website www.brivaloka.com
and We want to add more content and a cleaner design like these website
http://tarnwickfolvendale.com/
https://www.qmvorlu.com/

```html
<!DOCTYPE html>
<html lang="en">
<head>
<meta charset="utf-8">
<title>Contact Lenses – Brivaloka Optometry</title>
<link href="https://fonts.googleapis.com/css2?family=Nunito+Sans:wght@300;400;600;700;800&display=swap" rel="stylesheet">
<style>
:root{
  --teal:#0d8cb0;
  --yellow:#fbdc2e;
  --footer:#f9e25d;
  --band:#f1f1f1;
  --ink:#222;
  --body:#8a8a8a;
  --nav:#666;
  --dark:#2b2b2b;
}
*{margin:0;padding:0;box-sizing:border-box}
html,body{width:728px;height:1200px;overflow:hidden;background:#fff}
body{position:relative;font-family:"Nunito Sans",Arial,sans-serif;color:var(--ink)}
.abs{position:absolute}
.topbar{left:0;top:0;width:728px;height:32px;background:var(--teal)}
.topbar .cell{position:absolute;top:0;height:32px;border-left:1px solid rgba(255,255,255,.25);color:#fff;font-size:9px;display:flex;align-items:center;justify-content:center;gap:7px;white-space:nowrap}
.topbar .soc{width:32px}
.dot{display:block;width:6px;height:6px;border-radius:50%;background:var(--yellow)}
.logo{left:47px;top:13px;width:66px;height:88px;background:#fff;display:flex;flex-direction:column;align-items:center;justify-content:flex-end;padding-bottom:8px}
.logo .mark{width:40px;height:40px;background:var(--yellow);margin-bottom:8px}
.logo .name{font-size:9px;color:#555;letter-spacing:.5px;line-height:1}
.logo .sub{font-size:5.5px;color:#555;letter-spacing:1.2px;line-height:1.2}
.nav{left:0;top:0}
.nav span{position:absolute;top:67px;font-size:9.5px;color:var(--nav);white-space:nowrap;line-height:14px}
.nav .active{color:var(--teal)}
.search{left:669px;top:67px}
.band{left:0;top:114px;width:728px;height:82px;background:var(--band);display:flex;align-items:center;justify-content:center}
.band h1{font-size:22px;font-weight:800;color:var(--teal);letter-spacing:.3px}
.photo{left:47px;top:228px;width:306px;height:253px;background:linear-gradient(135deg,#f1e3e2 0%,#e9cfcf 40%,#c9dfe4 60%,#f3ece8 100%)}
.intro{left:381px;top:232px;width:272px}
.intro h2{font-size:13.5px;line-height:22px;font-weight:800;color:var(--teal)}
.intro .lead{margin-top:12px;font-size:8.5px;line-height:16px;font-weight:700;color:var(--ink)}
.intro .txt{margin-top:15px;font-size:8.5px;line-height:15.8px;font-weight:300;color:var(--body)}
.types{left:48px;top:526px;font-size:18px;font-weight:800;color:var(--teal)}
.card h3{font-size:13px;line-height:20px;font-weight:700;color:var(--dark)}
.card p{font-size:8.5px;line-height:15.8px;font-weight:300;color:var(--body)}
.btn{display:inline-flex;align-items:center;justify-content:center;width:107px;height:32px;background:var(--yellow);font-size:10.5px;color:var(--dark);letter-spacing:.3px}
.brands{top:776px;left:47px;width:634px;display:flex}
.brands div{width:105.6px;text-align:center;font-size:12px;font-weight:700;color:#111;letter-spacing:.5px;white-space:nowrap}
.frames{top:829px;left:47px;width:634px;display:flex}
.frames div{width:105.6px;display:flex;justify-content:center}
.frames span{display:block;width:72px;height:30px;border-radius:15px}
.footer{left:0;top:910px;width:728px;height:290px;background:var(--footer)}
.fcol{position:absolute;top:38px}
.fcol h4{font-size:12px;font-weight:700;color:var(--teal);margin-bottom:14px}
.frow{display:flex;gap:12px;font-size:9px;line-height:16px;color:#333;margin-bottom:9px}
.frow svg{flex:none;margin-top:2px}
.map{position:absolute;width:169px;height:25px;border-radius:13px;background:#2d2d2d;color:#fff;font-size:9px;display:flex;align-items:center;padding-left:11px;gap:12px;white-space:nowrap}
.hours{font-size:9px;color:#333;line-height:19px}
.hours b{font-weight:700}
.fsoc{position:absolute;top:1100px;left:479px;display:flex;gap:6px}
.fsoc span{width:25px;height:25px;border-radius:50%;background:#2d2d2d;display:flex;align-items:center;justify-content:center}
.fsoc span:first-child{background:var(--teal)}
.copyline{left:0;top:1156px;width:728px;border-top:1px solid rgba(0,0,0,.07)}
.copy{left:0;top:1172px;width:728px;text-align:center;font-size:8px;color:#555}
.copy b{color:var(--teal);font-weight:700}
</style>
</head>
<body>

<div class="abs topbar">
  <div class="cell" style="left:281px;width:103px">
    <svg width="11" height="11" viewBox="0 0 24 24" fill="none" stroke="#fbdc2e" stroke-width="2"><path d="M5 3h4l2 5-3 2a12 12 0 0 0 6 6l2-3 5 2v4a2 2 0 0 1-2 2A17 17 0 0 1 3 5a2 2 0 0 1 2-2z"/></svg>
    555-210-4418
  </div>
  <div class="cell" style="left:384px;width:171px">
    <svg width="12" height="9" viewBox="0 0 24 18" fill="none" stroke="#fbdc2e" stroke-width="2"><rect x="1" y="1" width="22" height="16"/><path d="M1 1l11 9 11-9"/></svg>
    info@brivalokaoptometry.com
  </div>
  <div class="cell soc" style="left:555px" aria-label="Social link"><span class="dot"></span></div>
  <div class="cell soc" style="left:587px" aria-label="Social link"><span class="dot"></span></div>
  <div class="cell soc" style="left:619px" aria-label="Social link"><span class="dot"></span></div>
  <div class="cell soc" style="left:651px;border-right:1px solid rgba(255,255,255,.25)" aria-label="Social link"><span class="dot"></span></div>
</div>

<div class="abs logo">
  <div class="mark"></div>
  <div class="name">BRIVALOKA</div>
  <div class="sub">OPTOMETRY</div>
</div>

<nav class="abs nav">
  <span style="left:134px">HOME</span>
  <span style="left:188px">OUR TEAM</span>
  <span class="active" style="left:260px">EYE CARE</span>
  <span style="left:326px">MYOPIA CONTROL CLINIC</span>
  <span style="left:473px">EYEWEAR</span>
  <span style="left:539px">BLOG</span>
  <span style="left:589px">CONTACT US</span>
</nav>
<svg class="abs search" width="12" height="12" viewBox="0 0 24 24" fill="none" stroke="#0d8cb0" stroke-width="2"><circle cx="10" cy="10" r="7"/><path d="M15 15l7 7"/></svg>

<div class="abs band"><h1>CONTACT LENSES</h1></div>

<div class="abs photo" role="img" aria-label="Close-up of an eye with a contact lens on a fingertip, soft pink and teal tones"></div>

<div class="abs intro">
  <h2>LOREM IPSUM IS SIMPLY DUMMY TEXT AND PRINTIGN TYPESETTING.</h2>
  <p class="lead">Scleral contacts are large-diameter gas permeable contact lenses specially designed to vault over the entire corneal surface and rest on the "white" of the eye (sclera).</p>
  <p class="txt">In doing so, scleral lenses functionally replace the irregular cornea with a perfectly smooth optical surface to correct vision problems caused by keratoconus and other corneal irregularities.<br>Also, the space between the cornea and the back surface of a scleral lens acts as a fluid reservoir to provide comfort for people with severe dry eyes who otherwise could not tolerate contact lens wear.</p>
</div>

<h2 class="abs types">TYPES OF SCLERAL</h2>

<div class="abs card" style="left:48px;top:568px;width:290px">
  <h3>SCLERAL FOR KERATOCONUS</h3>
  <p style="margin-top:4px">Dr. Nessa Vorin recommend scleral contact lenses for a variety of hard-to-fit eyes, including eyes with keratoconus. In cases of early keratoconus, a standard GP lens may be used...</p>
</div>
<div class="abs btn" style="left:47px;top:654px">LEARN MORE</div>

<div class="abs card" style="left:396px;top:568px;width:292px">
  <h3>SCLERAL CONTACT LENSES FOR DRY EYES AND OTHER EYE PROBLEMS</h3>
  <p style="margin-top:8px">In addition to keratoconus, scleral contact lenses can be used for eyes that have undergone a cornea transplant, and for people with severe dry eyes caused by conditions such as Sjogren's...</p>
</div>
<div class="abs btn" style="left:394px;top:679px">LEARN MORE</div>

<div class="abs brands">
  <div>VELMO</div><div>ARLO KENT</div><div>MARISOL &amp; CO.</div><div>OSTRADA</div><div>BELVAINE</div><div>KESTREL</div>
</div>
<div class="abs frames">
  <div><span role="img" aria-label="Sunglasses with blue lenses" style="background:linear-gradient(#4a6a96,#9bb3cf)"></span></div>
  <div><span role="img" aria-label="Round tortoiseshell eyeglasses" style="background:linear-gradient(#6b3b1e,#c69a74)"></span></div>
  <div><span role="img" aria-label="Round brown gradient sunglasses" style="background:linear-gradient(#7b5544,#e3cfc2)"></span></div>
  <div><span role="img" aria-label="Thin gold wire eyeglasses" style="background:linear-gradient(#e6d3b3,#f7f1e6)"></span></div>
  <div><span role="img" aria-label="Black cat-eye eyeglasses" style="background:linear-gradient(#222,#bbb)"></span></div>
  <div><span role="img" aria-label="White frame brown lens sunglasses" style="background:linear-gradient(#b28a6a,#e8e8e8)"></span></div>
</div>

<footer class="abs footer">
  <div class="fcol" style="left:48px">
    <h4>Brivaloka Optometry</h4>
    <div class="frow"><svg width="12" height="12" viewBox="0 0 24 24" fill="#0d8cb0"><path d="M5 2h4l2 6-3 2a12 12 0 0 0 6 6l2-3 6 2v4a2 2 0 0 1-2 2A18 18 0 0 1 3 4a2 2 0 0 1 2-2z"/></svg>555-210-4418</div>
    <div class="frow"><svg width="13" height="12" viewBox="0 0 24 22" fill="#0d8cb0"><rect x="6" y="0" width="12" height="7"/><rect x="1" y="8" width="22" height="14" rx="2"/></svg>555-210-4470</div>
    <div class="frow"><svg width="13" height="10" viewBox="0 0 24 18" fill="#0d8cb0"><path d="M0 0h24v2L12 10 0 2z"/><path d="M0 5l12 8 12-8v13H0z"/></svg>info@brivaloka.com</div>
    <div class="frow"><svg width="12" height="13" viewBox="0 0 24 26" fill="#0d8cb0"><path d="M12 0a9 9 0 0 0-9 9c0 7 9 17 9 17s9-10 9-17a9 9 0 0 0-9-9zm0 13a4 4 0 1 1 0-8 4 4 0 0 1 0 8z"/></svg>4820 Fennimore Ave., Larkfield,<br>CA 90012</div>
  </div>
  <div class="fcol" style="left:264px">
    <h4>Alder Crest</h4>
    <div class="frow"><svg width="12" height="12" viewBox="0 0 24 24" fill="#0d8cb0"><path d="M5 2h4l2 6-3 2a12 12 0 0 0 6 6l2-3 6 2v4a2 2 0 0 1-2 2A18 18 0 0 1 3 4a2 2 0 0 1 2-2z"/></svg>555-388-9021</div>
    <div class="frow"><svg width="13" height="10" viewBox="0 0 24 18" fill="#0d8cb0"><path d="M0 0h24v2L12 10 0 2z"/><path d="M0 5l12 8 12-8v13H0z"/></svg>aldercrest@brivaloka.com</div>
    <div class="frow"><svg width="12" height="13" viewBox="0 0 24 26" fill="#0d8cb0"><path d="M12 0a9 9 0 0 0-9 9c0 7 9 17 9 17s9-10 9-17a9 9 0 0 0-9-9zm0 13a4 4 0 1 1 0-8 4 4 0 0 1 0 8z"/></svg>1290 Quillon St., Suite 4,<br>Alder Crest, CA 90077</div>
  </div>
  <div class="fcol" style="left:480px">
    <h4>Opening Hours</h4>
    <div class="hours">
      Monday - Thursday : <b>9 am - 6 pm</b><br>
      Friday : <b>8.30 am - 5 pm</b><br>
      Saturday &nbsp;: <b>8.30 am- 5 pm</b><br>
      Closed on <b>Sundays</b>
    </div>
    <div class="hours" style="line-height:13px;margin-top:4px">Please keep in mind we are closed<br>for <b>lunch 1-2 pm</b></div>
  </div>
  <div class="map" style="left:47px;top:190px">Get directions on the map
    <svg width="18" height="6" viewBox="0 0 18 6" fill="none" stroke="#1aa6cf" stroke-width="1.2"><path d="M0 3h17M14 0.5l3 2.5-3 2.5"/></svg></div>
  <div class="map" style="left:263px;top:190px">Get directions on the map
    <svg width="18" height="6" viewBox="0 0 18 6" fill="none" stroke="#1aa6cf" stroke-width="1.2"><path d="M0 3h17M14 0.5l3 2.5-3 2.5"/></svg></div>
</footer>

<div class="fsoc">
  <span aria-label="Social link"><i class="dot"></i></span>
  <span aria-label="Social link"><i class="dot"></i></span>
  <span aria-label="Social link"><i class="dot"></i></span>
  <span aria-label="Social link"><i class="dot"></i></span>
</div>

<div class="abs copyline"></div>
<div class="abs copy">Copyright © <b>BRIVALOKA OPTOMETRY</b> - 2019 . All right Resereved</div>

</body>
</html>
```